Brightcoat Painting Services Requires a New Responsive Site

Hi Designers,

Our current website is this www.brightcoatpainting.com.au for some idea.
I made it on Adobe Muse, its very basic.
I would like it to be redesigned to look more professional and also responsive. I actually know how to do html5 and css but I think others will do this much better than me.

I do not need content because I am a copywriter and would like to do all SEO and copy myself.

The most improtant things to remember is that the site cannot use a CMS
and the code needs to be understandable so that I can go in and add content later on and do SEO work.

Also the site requires an additional testimonial page. I would imagine a nice gallery would be a great addition too(something that I can add images too through html. Also in it is important for it to contain those brand images on the front page as it increases authority. I will attach them onto the brief.

Those two files of nearbyfind and tradeleafs are local directories where we have reviews so a placement of those on the testimonail page would make great sense. I will to the href myself.

Anyway, good luck!

I look forward to see your designs :D
Updates

I have just been informed that on this site websites are simply designed and not built (developed) if this is the case please stop working on your designs and spending more time on this project. I REQUIRE DEVELOPMENT ALSO AND HAVE ALREADY CONTACTED SUPPORT.

Target Market(s)

The target market is 30-75 high income earners.

Industry/Entity Type

Painting

Number of Pages Required

5+ page

Font styles to use
Serif
Sans Serif

Requirements
Must have
• attractive gallery, and the brand icons uploaded.
• must be responsive
• web carousel (with the different types of work we do). eg domestic, commercial, industrial etc.
Nice to have
• a little interactivity
• corporate a natural design that goes well with our logo
Should not have
• any content. just write jiberish to fill in the spaces.
• I will be doing all copy and SEO myself.
• More than five pages, bascially the four that already exist plus the testimonail one.

```html
<!DOCTYPE html>
<html lang="en">
<head>
<meta charset="utf-8">
<title>Brightcoat Painting</title>
<link href="https://fonts.googleapis.com/css2?family=Open+Sans:wght@300;400;500;600&display=swap" rel="stylesheet">
<style>
:root{
  --brand:#3a7596;
  --brand-light:#41a9e0;
  --nav:#666;
  --text:#6b6b6b;
  --rule:#dcdcdc;
  --btn-grey-top:#8a8a8a;
  --btn-grey-bottom:#5c5c5c;
  --btn-blue-top:#3fb0ec;
  --btn-blue-bottom:#1f8fd0;
  --info-band:#f3f3f3;
  --footer:#2e2e2e;
  --footer-text:#c9c9c9;
  --icon:#9a9a9a;
}
*{margin:0;padding:0;box-sizing:border-box}
html,body{width:1086px;height:1200px;overflow:hidden;background:#fff}
body{font-family:"Open Sans",sans-serif;color:var(--text)}
.page{position:relative;width:1086px;height:1200px;overflow:hidden}

.site-header{position:absolute;left:0;top:0;width:1086px;height:133px}
.brand{position:absolute;left:92px;top:26px;display:flex;align-items:center;gap:12px}
.brand-square{width:78px;height:78px;background:var(--brand)}
.brand-name{font-weight:300;font-size:38px;line-height:40px;color:var(--brand)}
.header-phone{position:absolute;right:91px;top:36px;font-size:20px;color:var(--brand);display:flex;align-items:center;gap:4px}
.main-nav{position:absolute;right:90px;top:90px;display:flex;gap:38px}
.main-nav a{font-size:13.5px;text-decoration:none;color:var(--nav);text-transform:uppercase}
.main-nav a.is-active{color:var(--brand-light)}

.hero{position:absolute;left:0;top:133px;width:1086px;height:434px;
  background:linear-gradient(180deg,#b9b7b2 0%,#d8d3cb 35%,#8c6a58 70%,#6e4a3a 100%)}
.hero-arrow{position:absolute;top:192px;width:40px;height:52px;background:rgba(30,30,30,.75);display:flex;align-items:center;justify-content:center}
.hero-arrow.prev{left:0}
.hero-arrow.next{right:0}

.welcome{position:absolute;left:92px;top:604px;width:432px}
.section-title{font-weight:500;font-size:20px;color:var(--brand)}
.welcome p{margin-top:8px;font-size:13px;line-height:21px}
.partners{position:absolute;left:92px;top:733px;display:flex;align-items:center;gap:12px}
.partner{display:flex;align-items:center;gap:5px;font-size:12px;font-weight:600;color:#333}
.partner-square{width:40px;height:43px;background:#f2d21b}
.partner-square.blue{background:#1fa3dc}
.partner-circle{width:36px;height:36px;border-radius:50%;background:#1c3f7a}
.vrule{position:absolute;left:543px;top:612px;width:1px;height:168px;background:var(--rule)}

.services{position:absolute;left:571px;top:604px}
.service-grid{position:absolute;left:569px;top:646px;display:grid;grid-template-columns:208px 208px;gap:11px 11px}
.service-btn{height:56px;border-radius:2px;display:flex;align-items:center;gap:8px;padding-left:12px;
  color:#fff;font-size:18px;text-decoration:none;background:linear-gradient(180deg,var(--btn-grey-top),var(--btn-grey-bottom))}
.service-btn.is-active{background:linear-gradient(180deg,var(--btn-blue-top),var(--btn-blue-bottom))}

.hrule{position:absolute;left:92px;top:815px;width:905px;height:1px;background:var(--rule)}
.gallery-title{position:absolute;left:0;width:1086px;top:850px;text-align:center}
.gallery-strip{position:absolute;left:110px;top:893px;display:flex;gap:3px}
.gallery-thumb{width:142px;height:93px}
.gallery-arrow{position:absolute;top:930px;width:17px;height:20px;background:#b5b5b5;display:flex;align-items:center;justify-content:center}
.gallery-arrow.prev{left:90px;border-radius:10px 0 0 10px}
.gallery-arrow.next{left:980px;border-radius:0 10px 10px 0}

.contact-band{position:absolute;left:0;top:1021px;width:1086px;height:87px;background:var(--info-band);font-size:12.5px}
.contact-item{position:absolute;display:flex;align-items:center;gap:12px;color:#777}
.site-footer{position:absolute;left:0;top:1108px;width:1086px;height:92px;background:var(--footer);color:var(--footer-text);font-size:12px}
.footer-nav{position:absolute;left:92px;top:20px;display:flex;gap:12px}
.footer-nav a{color:var(--footer-text);text-decoration:none}
.copyright{position:absolute;left:92px;top:54px}
.social{position:absolute;right:91px;top:38px;display:flex;gap:9px}
.social span{width:23px;height:23px;border-radius:50%;background:#5e5e5e;display:flex;align-items:center;justify-content:center}
</style>
</head>
<body>
<div class="page">
  <header class="site-header">
    <div class="brand">
      <span class="brand-square"></span>
      <span class="brand-name">Brightcoat<br>Painting</span>
    </div>
    <div class="header-phone">
      <svg width="12" height="14" viewBox="0 0 12 14"><path d="M3 1 L5 4 L3.5 5.5 Q5 9 7.5 10.5 L9 9 L11.5 11 L10 13 Q4 12 1.5 3 Z" fill="#3a7596"/></svg>
      1300 555 274
    </div>
    <nav class="main-nav">
      <a href="#" class="is-active">Home</a>
      <a href="#">About us</a>
      <a href="#">Services</a>
      <a href="#">Gallery</a>
      <a href="#">Contact us</a>
    </nav>
  </header>

  <section class="hero" role="img" aria-label="Photo of a painter on a ladder working on a brick and weatherboard house">
    <span class="hero-arrow prev"><svg width="16" height="30"><path d="M14 1 L2 15 L14 29" stroke="#fff" stroke-width="2" fill="none"/></svg></span>
    <span class="hero-arrow next"><svg width="16" height="30"><path d="M2 1 L14 15 L2 29" stroke="#fff" stroke-width="2" fill="none"/></svg></span>
  </section>

  <section class="welcome">
    <h2 class="section-title">Welcome to Brightcoat Painting</h2>
    <p>Brightcoat Painting Services is a Melbourne family owned Painting &amp; Decorating business based in Harlow Bend, in the south east of Melbourne. We proudly provide domestic and commercial painting services across all suburbs of metropolitan Melbourne.</p>
  </section>
  <div class="partners">
    <span class="partner"><span class="partner-square"></span></span>
    <span class="partner">Colourmix</span>
    <span class="partner">Paintwell</span>
    <span class="partner"><span class="partner-square blue"></span></span>
    <span class="partner"><span class="partner-circle"></span></span>
    <span class="partner">Hallmere</span>
  </div>
  <div class="vrule"></div>

  <section class="services">
    <h2 class="section-title">Our Services</h2>
  </section>
  <div class="service-grid">
    <a href="#" class="service-btn is-active"><svg width="8" height="13"><path d="M1 1 L6 6.5 L1 12" stroke="#fff" stroke-width="1.6" fill="none"/></svg>Domestic Services</a>
    <a href="#" class="service-btn"><svg width="8" height="13"><path d="M1 1 L6 6.5 L1 12" stroke="#fff" stroke-width="1.6" fill="none"/></svg>Commercial Services</a>
    <a href="#" class="service-btn"><svg width="8" height="13"><path d="M1 1 L6 6.5 L1 12" stroke="#fff" stroke-width="1.6" fill="none"/></svg>Industrial Services</a>
    <a href="#" class="service-btn"><svg width="8" height="13"><path d="M1 1 L6 6.5 L1 12" stroke="#fff" stroke-width="1.6" fill="none"/></svg>Heritage Services</a>
  </div>

  <div class="hrule"></div>
  <h2 class="section-title gallery-title">Our Gallery</h2>
  <span class="gallery-arrow prev"><svg width="6" height="9"><path d="M5 1 L1 4.5 L5 8" stroke="#fff" stroke-width="1.5" fill="none"/></svg></span>
  <div class="gallery-strip">
    <div class="gallery-thumb" role="img" aria-label="Timber-lined room ready for painting" style="background:linear-gradient(180deg,#8a7a60,#c8a878)"></div>
    <div class="gallery-thumb" role="img" aria-label="Interior room with timber window frames" style="background:linear-gradient(180deg,#6a4a38,#b89a80)"></div>
    <div class="gallery-thumb" role="img" aria-label="Bathroom with timber vanity" style="background:linear-gradient(180deg,#4a2a20,#8a6a58)"></div>
    <div class="gallery-thumb" role="img" aria-label="Floor tiles with masking tape along the edge" style="background:linear-gradient(180deg,#c8c0a8,#5a5a50)"></div>
    <div class="gallery-thumb" role="img" aria-label="Painter working on a terracotta tiled roof" style="background:linear-gradient(180deg,#b8c8d8,#b85a40)"></div>
    <div class="gallery-thumb" role="img" aria-label="Freshly painted weatherboard house" style="background:linear-gradient(180deg,#c8d4dc,#8a7a68)"></div>
  </div>
  <span class="gallery-arrow next"><svg width="6" height="9"><path d="M1 1 L5 4.5 L1 8" stroke="#fff" stroke-width="1.5" fill="none"/></svg></span>

  <section class="contact-band">
    <div class="contact-item" style="left:112px;top:30px">
      <svg width="22" height="26" viewBox="0 0 22 26"><rect x="1" y="1" width="20" height="24" fill="none" stroke="#9a9a9a" stroke-width="2"/><rect x="7" y="4" width="8" height="12" fill="#9a9a9a"/></svg>
      <span>Harlow Bend, Victoria 3990,<br>Australia</span>
    </div>
    <div class="contact-item" style="left:334px;top:30px">
      <svg width="26" height="26" viewBox="0 0 26 26"><path d="M4 2 L9 7 L6.5 10 Q10 16 16 19.5 L19 17 L24 22 L21 25 Q8 22 1 5 Z" fill="#9a9a9a"/></svg>
      <span>Phone: 1300 555 274</span>
    </div>
    <div class="contact-item" style="left:551px;top:36px">
      <svg width="25" height="17" viewBox="0 0 25 17"><rect width="25" height="17" fill="#9a9a9a"/><path d="M0 0 L12.5 9 L25 0" stroke="#f3f3f3" stroke-width="1.5" fill="none"/></svg>
      <span>E-mail : info@brightcoatpainting.com.au</span>
    </div>
    <div class="contact-item" style="left:862px;top:38px">
      <span>ABN. 12 345 678 901</span>
    </div>
  </section>

  <footer class="site-footer">
    <nav class="footer-nav">
      <a href="#">Home</a><span>|</span>
      <a href="#">About us</a><span>|</span>
      <a href="#">Services</a><span>|</span>
      <a href="#">Gallery</a><span>|</span>
      <a href="#">Contact us</a>
    </nav>
    <p class="copyright">Copyright &copy; 2014 &nbsp;Brightcoat Painting. &nbsp;All rights reserved.</p>
    <div class="social">
      <span></span>
      <span></span>
      <span></span>
      <span><svg width="12" height="9" viewBox="0 0 12 9"><rect x=".5" y=".5" width="11" height="8" fill="none" stroke="#2e2e2e"/><path d="M.5 .5 L6 5 L11.5 .5" stroke="#2e2e2e" fill="none"/></svg></span>
    </div>
  </footer>
</div>
</body>
</html>
```